Profesional personal website needs design and business card

I need a business card with my professional name as a logo "Dorian Vitality" for my business. I am a Wellness Coach, consultant and trainer. So it should be professional, wellness oriented and modern.

Target Market(s)

Private clients, governments, corporations. Luxury and high market.

Industry/Entity Type

Health And Wellness

Contact Information for Business Card

Dorian Vitality should be the logo

Colors

Designer to choose colors to be used in the design.

Requirements
Must have
• Dorian Vitality
• Name: Tomás Lirandel
• Wellness Coach, Consultant & Trainer.
• Website: www.dorianvitality-example.com
• Phone:
• Spain (+34) 612 480 317
• (USA) +1 (555) 610 4829
Nice to have
• The most important is the design of "Dorian Vitality", as this is going to be my personal brand logo. It should be professional, wellness, high end and actual.
Should not have
• no golds, no baroque style..

```html
<!DOCTYPE html>
<html lang="en">
<head>
<meta charset="utf-8">
<title>Dorian Vitality — Business Card</title>
<link rel="stylesheet" href="https://fonts.googleapis.com/css2?family=Arimo:wght@400;700&display=swap">
<style>
  :root {
    --sky: #55bbdc;
    --sky-deep: #4aaed0;
    --ink: #5a5a5c;
    --paper: #f4f4f4;
    --paper-shade: #e9e9e9;
    --stage: #d9dadb;
    --white: #ffffff;
  }
  * { box-sizing: border-box; margin: 0; padding: 0; }
  html, body { width: 1200px; height: 1021px; overflow: hidden; }
  body {
    background: var(--stage);
    font-family: "Arimo", Arial, sans-serif;
    position: relative;
  }
  .card {
    position: absolute;
    left: 250px;
    width: 700px;
    height: 400px;
    box-shadow: 0 6px 18px rgba(0,0,0,0.18);
  }
  .card--back {
    top: 70px;
    background: linear-gradient(160deg, var(--sky-deep), var(--sky));
  }
  .card--front {
    top: 540px;
    background: linear-gradient(120deg, var(--paper-shade), var(--paper) 60%, var(--white));
  }

  /* Brand wordmark */
  .brand {
    display: flex;
    align-items: center;
    gap: 14px;
    font-weight: 700;
    letter-spacing: 1px;
    text-transform: uppercase;
  }
  .brand__dot { border-radius: 50%; flex: none; }
  .card--back .brand {
    position: absolute;
    left: 50%; top: 50%;
    transform: translate(-50%, -50%);
    color: var(--white);
    font-size: 34px;
  }
  .card--back .brand__dot { width: 30px; height: 30px; background: var(--white); }
  .card--front .brand {
    position: absolute;
    left: 44px; top: 42px;
    color: var(--sky);
    font-size: 24px;
  }
  .card--front .brand__dot { width: 22px; height: 22px; background: var(--sky); }

  /* Person */
  .person {
    position: absolute;
    left: 44px; top: 200px;
  }
  .person__tab {
    position: absolute;
    left: -44px; top: 0;
    width: 18px; height: 68px;
    background: var(--sky);
    border-radius: 0 5px 5px 0;
  }
  .person__name {
    color: var(--sky);
    font-weight: 700;
    font-size: 26px;
    margin-bottom: 6px;
  }
  .person__role {
    color: var(--ink);
    font-size: 19px;
    line-height: 1.25;
  }

  /* Contact */
  .contact {
    position: absolute;
    right: 40px; bottom: 36px;
    list-style: none;
    color: var(--ink);
    font-size: 19px;
    line-height: 1.3;
  }
  .contact__item { display: flex; align-items: center; gap: 8px; }
  .contact__icon { width: 16px; height: 16px; flex: none; }
  .contact__country { color: var(--sky); margin-left: 6px; }
</style>
</head>
<body>

<section class="card card--back" aria-label="Business card back">
  <div class="brand"><span class="brand__dot"></span>Dorian Vitality</div>
</section>

<section class="card card--front" aria-label="Business card front">
  <div class="brand"><span class="brand__dot"></span>Dorian Vitality</div>

  <div class="person">
    <span class="person__tab"></span>
    <p class="person__name">Tomás Lirandel</p>
    <p class="person__role">Wellness Coach<br>Consultant &amp; Trainer</p>
  </div>

  <ul class="contact">
    <li class="contact__item">
      <svg class="contact__icon" viewBox="0 0 24 24" aria-hidden="true"><path fill="#55bbdc" d="M6.6 10.8a15 15 0 0 0 6.6 6.6l2.2-2.2c.3-.3.7-.4 1-.2 1.1.4 2.3.6 3.6.6.6 0 1 .4 1 1V20c0 .6-.4 1-1 1A17 17 0 0 1 3 4c0-.6.4-1 1-1h3.5c.6 0 1 .4 1 1 0 1.3.2 2.5.6 3.6.1.3 0 .7-.2 1z"/></svg>
      (+34) 612 480 317<span class="contact__country">Spain</span>
    </li>
    <li class="contact__item">
      <svg class="contact__icon" viewBox="0 0 24 24" aria-hidden="true"><path fill="#55bbdc" d="M6.6 10.8a15 15 0 0 0 6.6 6.6l2.2-2.2c.3-.3.7-.4 1-.2 1.1.4 2.3.6 3.6.6.6 0 1 .4 1 1V20c0 .6-.4 1-1 1A17 17 0 0 1 3 4c0-.6.4-1 1-1h3.5c.6 0 1 .4 1 1 0 1.3.2 2.5.6 3.6.1.3 0 .7-.2 1z"/></svg>
      +1 (555) 610 4829<span class="contact__country">USA</span>
    </li>
    <li class="contact__item">
      <svg class="contact__icon" viewBox="0 0 24 24" aria-hidden="true"><g fill="none" stroke="#55bbdc" stroke-width="2"><circle cx="12" cy="12" r="9"/><ellipse cx="12" cy="12" rx="4" ry="9"/><path d="M3 12h18M5 7h14M5 17h14"/></g></svg>
      www.dorianvitality-example.com
    </li>
  </ul>
</section>

</body>
</html>
```